High Tech Real Estate Startup needs a business card

We are developing an innovative real estate marketing product based around advanced search and virtual reality.

We talk to people, we need business cards.

Target Market(s)

The target market is technology professionals and realtors.

Contact Information for Business Card

The information to be included will include

Name
Title
Phone Number
E-mail Address
www.zelquin.com

It should use simple iconography for each one of those fields.

Font styles to use
Other font styles liked:
• Co, Jubilat, Avenir

Colors

Designer to choose colors to be used in the design.

Requirements
Must have
• Clean aesthetic,
• Good use of negative space.
• It should use our company logo, shown in the attached file. It is able to use the negative of that logo (coloured font and white background) and I have attached other acceptable accent colours in a swatch file.
Should not have
• Should not be too busy
• No extraneous text (slogans, tag lines etc)

```html
<!DOCTYPE html>
<html lang="en">
<head>
<meta charset="utf-8">
<title>Zelquin Business Card</title>
<link rel="stylesheet" href="https://fonts.googleapis.com/css2?family=Work+Sans:wght@400;500&display=swap">
<style>
  :root {
    --backdrop: #2a2a2c;
    --card: #1b1b1d;
    --card-edge: #232325;
    --accent: #19c2c6;
    --ink: #f2f2f2;
    --emboss: #8a8a8d;
  }
  * { margin: 0; padding: 0; box-sizing: border-box; }
  html, body {
    width: 1200px;
    height: 900px;
    overflow: hidden;
    background: var(--backdrop);
    font-family: "Work Sans", Arial, sans-serif;
  }
  .canvas {
    width: 1200px;
    height: 900px;
    display: flex;
    flex-direction: column;
    align-items: center;
    justify-content: center;
    gap: 40px;
  }
  .card {
    width: 700px;
    height: 400px;
    background: linear-gradient(160deg, var(--card-edge), var(--card));
    position: relative;
  }
  .card-front {
    display: flex;
    align-items: center;
    justify-content: center;
  }
  .wordmark {
    font-weight: 500;
    letter-spacing: 2px;
    line-height: 1;
  }
  .card-front .wordmark {
    font-size: 84px;
    color: var(--emboss);
  }
  .card-back {
    display: flex;
    align-items: center;
    padding: 0 0 0 80px;
  }
  .card-back .wordmark {
    font-size: 64px;
    color: var(--accent);
    width: 300px;
  }
  .divider {
    width: 2px;
    height: 150px;
    background: var(--accent);
    margin: 0 36px 0 20px;
  }
  .contact { color: var(--ink); }
  .contact-name {
    color: var(--accent);
    font-size: 22px;
    font-weight: 500;
    letter-spacing: 0.5px;
    text-transform: uppercase;
  }
  .contact-title { font-size: 16px; margin-bottom: 12px; }
  .contact-address { font-size: 16px; line-height: 1.3; margin-bottom: 6px; }
  .contact-line {
    display: flex;
    align-items: center;
    gap: 8px;
    font-size: 17px;
    line-height: 1.45;
    list-style: none;
  }
  .contact-line svg { width: 12px; height: 12px; flex: none; }
</style>
</head>
<body>
<main class="canvas">
  <section class="card card-front">
    <span class="wordmark">ZELQUIN</span>
  </section>

  <section class="card card-back">
    <span class="wordmark">ZELQUIN</span>
    <div class="divider"></div>
    <div class="contact">
      <p class="contact-name">Dana Whitfield</p>
      <p class="contact-title">Director</p>
      <p class="contact-address">860 Alder Ridge Rd.<br>Franklin, TN 37064</p>
      <ul>
        <li class="contact-line">
          <svg viewBox="0 0 12 12" aria-hidden="true"><path d="M2.5 1 L4.5 1 L5.2 3.6 L4 4.6 Q5 7 7.4 8 L8.4 6.8 L11 7.5 L11 9.5 Q10.5 11 9 11 Q1 10 1 3 Q1 1.5 2.5 1 Z" fill="var(--accent)"/></svg>
          +1-555-204-7318
        </li>
        <li class="contact-line">
          <svg viewBox="0 0 12 12" aria-hidden="true"><rect x="1" y="2.5" width="10" height="7" fill="none" stroke="var(--accent)" stroke-width="1.2"/><path d="M1 2.5 L6 6.5 L11 2.5" fill="none" stroke="var(--accent)" stroke-width="1.2"/></svg>
          info@zelquin.com
        </li>
        <li class="contact-line">
          <svg viewBox="0 0 12 12" aria-hidden="true"><circle cx="6" cy="6" r="5" fill="none" stroke="var(--accent)" stroke-width="1.1"/><ellipse cx="6" cy="6" rx="2.2" ry="5" fill="none" stroke="var(--accent)" stroke-width="1"/><path d="M1 6 H11" stroke="var(--accent)" stroke-width="1"/></svg>
          www.zelquin.com
        </li>
      </ul>
    </div>
  </section>
</main>
</body>
</html>
```